Business Card Design

Velora Pixel Outreach

An online marketing consulting & strategy business for the cosmetic niche

We specialise in Increasing Leads, Conversions & Content Marketing

I am looking for a very clean, BOLD business card that is simple & effective

Target Market(s)

cosmetic surgeons & cosmetic clinics

Industry/Entity Type

Marketing

Contact Information for Business Card

Dermot Kalway
Online Marketing Strategist

Dermot@VeloraPixelOutreach.example
0492 158 620

LinkedIn: in/dermotkalway

```html
<!DOCTYPE html>
<html lang="en">
<head>
<meta charset="utf-8">
<title>Velora Pixel Outreach – Business Card</title>
<link rel="stylesheet" href="https://fonts.googleapis.com/css2?family=Saira:wght@500;600&family=Open+Sans:wght@600&display=swap">
<style>
  :root {
    --stage: #a9a8a9;
    --sky: #34a9df;
    --lime: #a2cc3a;
    --ink: #5d6166;
    --white: #ffffff;
    --rule: #8fb7cf;
  }
  * { box-sizing: border-box; margin: 0; padding: 0; }
  html, body { width: 1200px; height: 900px; overflow: hidden; }
  body { background: var(--stage); position: relative; font-family: "Open Sans", Arial, sans-serif; }

  .card { position: absolute; overflow: hidden; box-shadow: 3px 4px 6px rgba(0,0,0,.35); }
  .card--rounded { border-radius: 26px; }

  .card-back { background: linear-gradient(to bottom, var(--sky) 0%, #6fb8a8 45%, var(--lime) 100%); }
  .back-1 { left: 18px; top: 110px; width: 566px; height: 340px; }
  .back-2 { left: 18px; top: 486px; width: 566px; height: 326px; }
  .front-1 { left: 612px; top: 110px; width: 564px; height: 340px; }
  .front-2 { left: 612px; top: 484px; width: 568px; height: 328px; }

  .brand { position: absolute; display: flex; align-items: center; gap: 14px; }
  .brand-dot { border-radius: 50%; flex: none; }
  .brand-name { font-family: "Saira", Arial, sans-serif; font-weight: 600; text-transform: uppercase; line-height: .92; }

  .card-back .brand { left: 106px; top: 50%; transform: translateY(-50%); }
  .card-back .brand-dot { width: 96px; height: 96px; border: 10px solid var(--white); }
  .card-back .brand-name { color: var(--white); font-size: 34px; letter-spacing: 6px; }

  .front-art { position: absolute; inset: 0; width: 100%; height: 100%; }
  .card-front .brand { left: 158px; top: 64px; gap: 10px; }
  .card-front .brand-dot { width: 52px; height: 52px; border: 6px solid var(--sky); }
  .card-front .brand-name { color: var(--ink); font-size: 20px; letter-spacing: 3px; }

  .person { position: absolute; left: 47px; top: 180px; }
  .person-name { font-size: 21px; font-weight: 600; padding-bottom: 2px; border-bottom: 1.5px solid var(--rule); display: inline-block; }
  .person-name .first { color: var(--sky); }
  .person-name .last { color: var(--lime); }
  .person-role { margin-top: 6px; font-size: 13px; color: var(--ink); }

  .contact-divider { position: absolute; left: 230px; top: 170px; width: 2px; height: 82px; background: linear-gradient(var(--sky), var(--lime)); }
  .contacts { position: absolute; left: 246px; top: 168px; list-style: none; }
  .contacts li { display: flex; align-items: center; gap: 9px; height: 32px; font-size: 13px; color: var(--ink); }
  .contact-icon { width: 18px; height: 18px; flex: none; }
</style>
</head>
<body>

  <section class="card card-back back-1">
    <div class="brand">
      <span class="brand-dot"></span>
      <span class="brand-name">Velora<br>Pixel<br>Outreach</span>
    </div>
  </section>

  <section class="card card-back card--rounded back-2">
    <div class="brand">
      <span class="brand-dot"></span>
      <span class="brand-name">Velora<br>Pixel<br>Outreach</span>
    </div>
  </section>

  <section class="card card-front front-1">
    <svg class="front-art" viewBox="0 0 564 340" preserveAspectRatio="none" aria-hidden="true">
      <defs>
        <linearGradient id="band-top" x1="0" y1="0" x2="0" y2="1">
          <stop offset="0" stop-color="#34a9df"/><stop offset="0.22" stop-color="#a2cc3a"/><stop offset="1" stop-color="#a2cc3a"/>
        </linearGradient>
        <linearGradient id="band-bottom" x1="0" y1="0" x2="0" y2="1">
          <stop offset="0" stop-color="#a2cc3a"/><stop offset="0.76" stop-color="#34a9df"/><stop offset="1" stop-color="#a2cc3a"/>
        </linearGradient>
      </defs>
      <rect x="0" y="0" width="564" height="170" fill="url(#band-top)"/>
      <rect x="0" y="170" width="564" height="170" fill="url(#band-bottom)"/>
      <path d="M18 38 L546 38 Q570 170 540 300 L24 300 Q-4 170 18 38 Z" fill="#ffffff"/>
      <circle cx="440" cy="170" r="118" fill="none" stroke="#eef3e4" stroke-width="26"/>
    </svg>
    <div class="brand"><span class="brand-dot"></span><span class="brand-name">Velora<br>Pixel<br>Outreach</span></div>
    <div class="person">
      <div class="person-name"><span class="first">Dermot</span> <span class="last">Kalway</span></div>
      <p class="person-role">Online Marketing Strategist</p>
    </div>
    <div class="contact-divider"></div>
    <ul class="contacts">
      <li><svg class="contact-icon" viewBox="0 0 18 18"><rect width="18" height="18" fill="#34a9df"/><circle cx="9" cy="9" r="6" fill="none" stroke="#fff" stroke-width="1.2"/><path d="M3 9h12M9 3v12M5 5.5h8M5 12.5h8" stroke="#fff" stroke-width="1"/></svg>0492 158 620</li>
      <li><svg class="contact-icon" viewBox="0 0 18 18"><rect width="18" height="18" fill="#34a9df"/><rect x="3" y="5" width="12" height="8" fill="none" stroke="#fff" stroke-width="1.2"/><path d="M3 5l6 5 6-5" fill="none" stroke="#fff" stroke-width="1.2"/></svg>Dermot@VeloraPixelOutreach.example</li>
      <li><svg class="contact-icon" viewBox="0 0 18 18"><rect width="18" height="18" fill="#34a9df"/></svg>in/dermotkalway</li>
    </ul>
  </section>

  <section class="card card-front card--rounded front-2">
    <svg class="front-art" viewBox="0 0 564 340" preserveAspectRatio="none" aria-hidden="true">
      <rect x="0" y="0" width="564" height="170" fill="url(#band-top)"/>
      <rect x="0" y="170" width="564" height="170" fill="url(#band-bottom)"/>
      <path d="M18 38 L546 38 Q570 170 540 300 L24 300 Q-4 170 18 38 Z" fill="#ffffff"/>
      <circle cx="440" cy="170" r="118" fill="none" stroke="#eef3e4" stroke-width="26"/>
    </svg>
    <div class="brand"><span class="brand-dot"></span><span class="brand-name">Velora<br>Pixel<br>Outreach</span></div>
    <div class="person">
      <div class="person-name"><span class="first">Dermot</span> <span class="last">Kalway</span></div>
      <p class="person-role">Online Marketing Strategist</p>
    </div>
    <div class="contact-divider"></div>
    <ul class="contacts">
      <li><svg class="contact-icon" viewBox="0 0 18 18"><rect width="18" height="18" fill="#34a9df"/><circle cx="9" cy="9" r="6" fill="none" stroke="#fff" stroke-width="1.2"/><path d="M3 9h12M9 3v12M5 5.5h8M5 12.5h8" stroke="#fff" stroke-width="1"/></svg>0492 158 620</li>
      <li><svg class="contact-icon" viewBox="0 0 18 18"><rect width="18" height="18" fill="#34a9df"/><rect x="3" y="5" width="12" height="8" fill="none" stroke="#fff" stroke-width="1.2"/><path d="M3 5l6 5 6-5" fill="none" stroke="#fff" stroke-width="1.2"/></svg>Dermot@VeloraPixelOutreach.example</li>
      <li><svg class="contact-icon" viewBox="0 0 18 18"><rect width="18" height="18" fill="#34a9df"/></svg>in/dermotkalway</li>
    </ul>
  </section>

</body>
</html>
```